Webdesign für Hunde- und Katzenernährungsberatung
Zielgruppe
Hunde und Katzenernährungsberatung, für Menschen, die auch bei ihren Hunden und Katzen auf gesunde, natürliche Ernährung achten wollen, ohne unnötigen Geschmacksverstärker, Zucker, Zusatzstoffe, etc. die gesundheitliche Probleme bei den Tieren verursachen können.
Umstellung auf natürliche, artgerechte Fütterung, teils roh, teils gekocht, angepasst auf Grösse, Rasse, Alter etc., auch speziell für Welpen
Beratung bei:
Übergewicht
Allergien
Unverträglichkeiten
Magen-Darm Problemen
individuelle Ernährungspläne
Selbsthergestellte Kekse, Leckerlies, Snacks, Pralinen und div. Hausmannskost in Einmachgläsern (alles auf Vorbestellung).
Diverse Accessoires
Halsbänder, Leinen, Geschirr aus div. natürlichen Materialien
Lern- und Spielzeug aus Holz und Stoff
div. Zubehör für Tiere, sowie auch für Frauchen und Herrchen
Aufgabenstellung
Die Seite sollte stilvoll aber nicht überfüllt sein und im Retro/Vintage Stil gehalten werden, da das Logo bereits sehr wirksam und eher auffällig ist, dezente Töne im Hintergrund, die Nahrungsmittel werden dann ev. auf Schieferplatten oder unauffälligem Hintergrund platziert. Ich sollte zu einem späteren Zeitpunkt selber Fotos, Links, Texte, etc. einfach dazu fügen können.

```html
<!DOCTYPE html>
<html lang="de">
<head>
<meta charset="utf-8">
<title>Napfglück – Ernährungsberatung für Hund und Katze</title>
<link rel="stylesheet" href="https://fonts.googleapis.com/css2?family=Caveat+Brush&family=Open+Sans:wght@400;600;700&family=Open+Sans+Condensed:wght@300;700&display=swap">
<style>
  :root {
    --stage: #eceff2;
    --sky: #a8cae3;
    --sky-deep: #94bbd8;
    --paper: #ffffff;
    --ink: #2d2f33;
    --ink-soft: #5b6068;
    --orange: #d7893a;
    --orange-deep: #c47628;
    --brown: #6b4128;
    --button-blue: #7ea6c4;
  }
  * { box-sizing: border-box; margin: 0; padding: 0; }
  html, body { width: 1200px; height: 800px; overflow: hidden; }
  body {
    background: var(--stage);
    font-family: "Open Sans", sans-serif;
    color: var(--ink);
    position: relative;
  }

  /* ---------- mobile page ---------- */
  .mobile-page {
    position: absolute; left: 150px; top: 30px;
    width: 380px; height: 740px;
    background: var(--paper);
    overflow: hidden;
    box-shadow: 0 10px 30px rgba(40,60,80,.15);
  }
  .site-header {
    height: 64px; display: flex; align-items: center; justify-content: space-between;
    padding: 0 20px; background: var(--paper);
  }
  .brand { display: flex; align-items: center; gap: 8px;
    font-weight: 700; font-size: 17px; color: var(--brown); }
  .brand-dot { width: 14px; height: 14px; border-radius: 50%; background: var(--sky-deep); }
  .menu-icon { width: 22px; display: grid; gap: 4px; }
  .menu-icon span { height: 2px; background: var(--button-blue); display: block; }

  .hero {
    background: var(--sky);
    height: 376px; position: relative; text-align: center; padding-top: 26px;
  }
  .hero-rule { width: 230px; height: 1px; background: rgba(255,255,255,.8); margin: 0 auto; }
  .hero-rule--bottom { margin-top: 6px; }
  .hero-title {
    font-family: "Caveat Brush", cursive; font-weight: 400;
    font-size: 44px; line-height: 40px; color: var(--ink); margin: 8px 0 6px;
  }
  .hero-sub {
    font-family: "Open Sans Condensed", sans-serif; font-weight: 700;
    font-size: 10px; letter-spacing: .5px; color: var(--ink-soft); text-transform: uppercase;
  }
  .hero-button {
    display: inline-block; margin-top: 18px; padding: 5px 22px;
    background: var(--button-blue); color: var(--paper);
    font-size: 9px; font-weight: 700; letter-spacing: 1px; text-transform: uppercase;
  }
  .hero-art {
    position: absolute; left: 60px; right: 0; bottom: 0; height: 180px;
    background: linear-gradient(100deg, #e8a250 0%, #e39a45 45%, #7a4a2e 62%, #5d3722 100%);
  }

  .welcome { display: flex; height: 300px; background: var(--paper); }
  .portrait {
    width: 150px; height: 100%;
    background: linear-gradient(180deg, #e7ddd4 0%, #c9a98f 45%, #4a4f5c 100%);
  }
  .welcome-text { flex: 1; padding: 22px 18px 0 16px; }
  .welcome-title, .advice-title {
    font-family: "Caveat Brush", cursive; font-weight: 400;
    color: var(--orange); font-size: 24px; line-height: 24px;
  }
  .welcome-copy { font-size: 8.5px; line-height: 13px; color: var(--ink-soft); margin: 10px 0 14px; }
  .advice-list { list-style: none; font-family: "Open Sans Condensed", sans-serif; font-weight: 700;
    font-size: 10px; line-height: 14px; text-transform: uppercase; color: var(--ink-soft); margin-top: 6px; }

  /* ---------- shop page ---------- */
  .shop-page {
    position: absolute; left: 590px; top: 30px;
    width: 470px; height: 740px; overflow: hidden;
    background: var(--sky);
    box-shadow: 0 10px 30px rgba(40,60,80,.15);
  }
  .shop-intro {
    background: var(--paper); padding: 30px 40px 28px;
    border-bottom: 2px solid var(--sky-deep);
  }
  .shop-list { list-style: none; font-family: "Open Sans Condensed", sans-serif; font-weight: 700;
    font-size: 13px; line-height: 20px; text-transform: uppercase; color: var(--ink-soft); }
  .shop-button {
    display: inline-block; margin-top: 18px; padding: 6px 24px;
    background: var(--button-blue); color: var(--paper);
    font-size: 10px; font-weight: 700; letter-spacing: 1px; text-transform: uppercase;
  }
  .product-row { display: flex; justify-content: center; padding-top: 50px; }
  .product-card {
    width: 250px;
    background: var(--paper); padding: 16px 18px 20px; text-align: center;
    box-shadow: 0 6px 16px rgba(30,60,90,.18);
  }
  .product-image { height: 120px; background: linear-gradient(135deg, #a8623a 0%, #8a4a2a 55%, #6d3820 100%); }
  .product-name { font-family: "Open Sans Condensed", sans-serif; font-weight: 700; font-size: 12px;
    text-transform: uppercase; color: var(--orange); margin-top: 12px; text-align: left; }
  .dotted { border-top: 1px dotted var(--orange); margin: 7px 0; }
  .product-desc { font-size: 9px; line-height: 13px; color: var(--ink-soft); }
  .price { font-family: "Open Sans Condensed", sans-serif; font-weight: 700; font-size: 40px; color: var(--orange-deep); line-height: 44px; margin-top: 6px; }
  .price-note { font-size: 8px; color: var(--ink-soft); line-height: 12px; }
  .price-note .accent { color: var(--orange); }
  .add-to-cart { display: inline-block; margin-top: 14px; padding: 7px 26px;
    background: var(--orange); color: var(--paper); font-family: "Open Sans Condensed", sans-serif;
    font-weight: 700; font-size: 12px; text-transform: uppercase; letter-spacing: .5px; }
</style>
</head>
<body>

<section class="mobile-page">
  <header class="site-header">
    <div class="brand"><span class="brand-dot"></span>Napfglück</div>
    <div class="menu-icon"><span></span><span></span><span></span></div>
  </header>

  <div class="hero">
    <div class="hero-rule"></div>
    <h1 class="hero-title">Lorem ipsum<br>dolor sit amet</h1>
    <p class="hero-sub">Lorem ipsum dolor sit amet consectetur adipiscing elit</p>
    <div class="hero-rule hero-rule--bottom"></div>
    <span class="hero-button">Online Shop</span>
    <div class="hero-art" role="img" aria-label="Illustration: orange Katze und braun-weißer Hund sitzen nebeneinander"></div>
  </div>

  <div class="welcome">
    <div class="portrait" role="img" aria-label="Porträtfoto der Ernährungsberaterin"></div>
    <div class="welcome-text">
      <h2 class="welcome-title">Willkommen auf unserer Website</h2>
      <p class="welcome-copy">Lorem ipsum dolor sit amet, consectetur adipiscing elit, sed do eiusmod tempor incididunt ut labore et dolore magna aliqua. Ut enim ad minim veniam, quis nostrud exercitation ullamco laboris nisi ut aliquip ex ea commodo consequat.</p>
      <h3 class="advice-title">Beratung bei:</h3>
      <ul class="advice-list">
        <li>Übergewicht / Allergien</li>
        <li>Unverträglichkeiten</li>
        <li>Magen-Darm Problemen</li>
      </ul>
    </div>
  </div>
</section>

<section class="shop-page">
  <div class="shop-intro">
    <ul class="shop-list">
      <li>Leckerlies, Kekse und Snacks</li>
      <li>Geschirr, Leinen und Halsbänder</li>
      <li>Lern- und Spielzeug aus Holz</li>
      <li>Div. Zubehör für Tier und Mensch</li>
    </ul>
    <span class="shop-button">Mehr erfahren</span>
  </div>

  <div class="product-row">
    <article class="product-card">
      <div class="product-image" role="img" aria-label="Produktfoto: getrocknete Fleischwürfel als Leckerli"></div>
      <h4 class="product-name">Product name goes here</h4>
      <div class="dotted"></div>
      <p class="product-desc">Lorem ipsum dolor sit amet, consectetur adipiscing elit, sed do eiusmod tempor incididunt ut labore et dolore magna aliqua.</p>
      <div class="dotted"></div>
      <div class="price">€ 10,50</div>
      <p class="price-note">inkl. 19% MwSt. zzgl.<br><span class="accent">Versandkosten</span> | Lieferzeit 2–3 Tage</p>
      <span class="add-to-cart">Add to cart</span>
    </article>
  </div>
</section>

</body>
</html>
```